Business card for my new company (Accounting firm)

I need a business card for my new business Brightwell Advisory and Ledger SA. Our services are accounting, tax, audit and financial management. Our customers are small companies, start-ups and new companies. The final design has to show financial security, trust and growth. Please find our logo attached to the business card. Text for the business card: Brightwell Advisory and Ledger SA Tomas Varenholt Director and Founder Certified Accountant Tel. 022 418 57 34 tv@clairevalconseil.ch www.clairevalconseil.ch Rue des Vergières 27 1201 Geneva
Target Market(s)
Our customers are small companies, start-ups and new companies.
Industry/Entity Type
Finance And Accounting
Contact Information for Business Card
Claireval Conseil et Comptes SA
Tomas Varenholt
Directeur et Fondateur
Expert-comptable diplômé
Tél. 022 418 57 34
tv@clairevalconseil.ch
www.clairevalconseil.ch
Rue des Vergières 27
1201 Genève

```html
<!DOCTYPE html>
<html lang="fr">
<head>
<meta charset="utf-8">
<title>Claireval Conseil et Comptes – Carte de visite</title>
<link rel="stylesheet" href="https://fonts.googleapis.com/css2?family=Montserrat:wght@600&family=Roboto:wght@400;700&display=swap">
<style>
  :root {
    --backdrop: #3b3b3d;
    --card: #1e1e20;
    --card-emboss: #2e2e31;
    --brand-blue: #2a8fd8;
    --brand-blue-light: #35aee6;
    --text-light: #f4f4f4;
  }
  * { box-sizing: border-box; margin: 0; padding: 0; }
  html, body { width: 799px; height: 1200px; overflow: hidden; }
  body {
    background: var(--backdrop);
    font-family: "Roboto", Arial, sans-serif;
    position: relative;
  }
  .card {
    position: absolute;
    left: 90px;
    width: 620px;
    height: 380px;
    background: var(--card);
    border-radius: 4px;
    overflow: hidden;
  }
  .card--front { top: 130px; }
  .card--back { top: 690px; }

  .front-stripe {
    position: absolute;
    left: 0; right: 0; bottom: 0;
    height: 12px;
    background: var(--brand-blue-light);
  }
  .front-name {
    position: absolute;
    left: 0; right: 0; top: 150px;
    text-align: center;
    font-family: "Montserrat", Arial, sans-serif;
    font-weight: 600;
    font-size: 34px;
    letter-spacing: 3px;
    color: var(--card-emboss);
    line-height: 1.2;
  }

  .back-mark {
    position: absolute;
    left: 44px; top: 110px;
    width: 150px; height: 150px;
    background: var(--brand-blue);
    border-radius: 6px;
  }
  .back-info {
    position: absolute;
    right: 40px; top: 44px;
    width: 380px;
    text-align: right;
  }
  .company-name {
    font-family: "Montserrat", Arial, sans-serif;
    font-weight: 600;
    font-size: 26px;
    letter-spacing: 1.5px;
    color: var(--text-light);
    line-height: 1.2;
    margin-bottom: 30px;
  }
  .person-name {
    font-weight: 700;
    font-size: 24px;
    color: var(--brand-blue);
    margin-bottom: 4px;
  }
  .person-role {
    font-size: 15px;
    color: var(--text-light);
    line-height: 1.3;
    margin-bottom: 16px;
  }
  .contact-list { list-style: none; }
  .contact-item {
    display: flex;
    justify-content: flex-end;
    align-items: center;
    gap: 10px;
    font-size: 16px;
    color: var(--text-light);
    line-height: 1.5;
  }
  .contact-icon { width: 14px; height: 14px; flex: none; }
  .contact-icon--blank { visibility: hidden; }
</style>
</head>
<body>
  <section class="card card--front" aria-label="Recto de la carte">
    <p class="front-name">CLAIREVAL<br>CONSEIL ET COMPTES</p>
    <div class="front-stripe"></div>
  </section>

  <section class="card card--back" aria-label="Verso de la carte">
    <div class="back-mark"></div>
    <div class="back-info">
      <p class="company-name">CLAIREVAL<br>CONSEIL ET COMPTES</p>
      <p class="person-name">Tomas Varenholt</p>
      <p class="person-role">Directeur et Fondateur<br>Expert-comptable diplômé</p>
      <ul class="contact-list">
        <li class="contact-item">022 418 57 34
          <svg class="contact-icon" viewBox="0 0 16 16" aria-hidden="true"><path fill="#2a8fd8" d="M3 1h3l1.5 4-2 1.5a9 9 0 0 0 4 4L11 8.5l4 1.5v3a2 2 0 0 1-2 2A12 12 0 0 1 1 3a2 2 0 0 1 2-2z"/></svg>
        </li>
        <li class="contact-item">tv@clairevalconseil.ch
          <svg class="contact-icon" viewBox="0 0 16 16" aria-hidden="true"><rect x="1" y="3" width="14" height="10" rx="1" fill="#2a8fd8"/><path d="M1.5 3.5 8 9l6.5-5.5" stroke="#1e1e20" stroke-width="1.3" fill="none"/></svg>
        </li>
        <li class="contact-item">www.clairevalconseil.ch
          <svg class="contact-icon" viewBox="0 0 16 16" aria-hidden="true"><g fill="none" stroke="#2a8fd8" stroke-width="1.4"><circle cx="8" cy="8" r="6.5"/><ellipse cx="8" cy="8" rx="3" ry="6.5"/><path d="M1.5 8h13"/></g></svg>
        </li>
        <li class="contact-item">Rue des Vergières 27 1201 Genève
          <svg class="contact-icon contact-icon--blank" viewBox="0 0 16 16" aria-hidden="true"></svg>
        </li>
      </ul>
    </div>
  </section>
</body>
</html>
```